Business Card Design Project

I have established a company called "Corvella" which is a business specialising in psychotherapy/counselling , predominantly for anxiety & depression.

My name is Nel....hence, the Corvella link. However, Corvella was also chosen for its reference to green shoots of growth/recovery.

Corvella is to be "upmarket" and highly professional. I'm keen for the style and colours to reflect this.....taupe/grey with navy/black script, for example.....NO primary colours.

My name needs to be on the card and my mobile number. Not sure, but suspect it should also have my qualifications ( BA (Psych) & BSc (Hons) Psychology). Mobile number 0412 903 618.

```html
<!DOCTYPE html>
<html lang="en">
<head>
<meta charset="utf-8">
<title>Corvella – Business Card Front</title>
<link rel="stylesheet" href="https://fonts.googleapis.com/css2?family=Philosopher&family=Raleway:wght@200&family=Open+Sans:wght@400&display=swap">
<style>
  :root {
    --page-bg: #efefef;
    --brand-sage: #6f8f3a;
    --name-navy: #1f2a55;
    --ink-dark: #151a2c;
    --tagline-white: #ffffff;
    --taupe-light: #f5f2ed;
    --taupe-mid: #d3cabd;
    --taupe-deep: #a89a88;
    --navy: #26305e;
    --navy-deep: #161c3a;
    --umber: #5a5048;
    --umber-light: #8a7d70;
    --silver-light: #ffffff;
    --silver-mid: #b9bcc0;
    --silver-dark: #4a4d52;
  }
  html, body {
    margin: 0;
    padding: 0;
    width: 1026px;
    height: 1200px;
    overflow: hidden;
    background: var(--page-bg);
  }
  .canvas {
    position: relative;
    width: 1026px;
    height: 1200px;
  }
  .business-card {
    position: absolute;
    left: 61px;
    top: 350px;
    width: 903px;
    height: 500px;
    overflow: hidden;
  }
  .card-artwork {
    position: absolute;
    inset: 0;
    width: 100%;
    height: 100%;
    display: block;
  }
  .brand-name {
    position: absolute;
    left: 56px;
    top: 118px;
    margin: 0;
    font-family: "Philosopher", sans-serif;
    font-weight: 400;
    font-size: 64px;
    line-height: 1;
    color: var(--brand-sage);
  }
  .practitioner {
    position: absolute;
    right: 171px;
    top: 96px;
    text-align: right;
    margin: 0;
  }
  .practitioner-name {
    margin: 0 0 4px;
    font-family: "Raleway", sans-serif;
    font-weight: 200;
    font-size: 104px;
    line-height: 1;
    letter-spacing: 2px;
    color: var(--name-navy);
  }
  .credential,
  .mobile {
    margin: 0;
    font-family: "Open Sans", sans-serif;
    font-size: 30px;
    line-height: 44px;
    color: var(--ink-dark);
    letter-spacing: -0.5px;
  }
  .tagline {
    position: absolute;
    left: 66px;
    top: 398px;
    margin: 0;
    font-family: "Open Sans", sans-serif;
    font-size: 38px;
    line-height: 1;
    color: var(--tagline-white);
    letter-spacing: -0.3px;
  }
</style>
</head>
<body>
<main class="canvas">
  <section class="business-card" aria-label="Corvella business card, front">
    <svg class="card-artwork" viewBox="0 0 258 143" preserveAspectRatio="none" aria-hidden="true">
      <defs>
        <linearGradient id="taupe-ground" x1="0" y1="0" x2="1" y2="0">
          <stop offset="0" stop-color="var(--taupe-light)"/>
          <stop offset="0.18" stop-color="var(--taupe-mid)"/>
          <stop offset="0.45" stop-color="var(--taupe-deep)"/>
          <stop offset="1" stop-color="var(--taupe-deep)"/>
        </linearGradient>
        <linearGradient id="silver" x1="0" y1="0" x2="1" y2="0">
          <stop offset="0" stop-color="var(--silver-light)"/>
          <stop offset="0.45" stop-color="var(--silver-mid)"/>
          <stop offset="1" stop-color="var(--silver-dark)"/>
        </linearGradient>
        <linearGradient id="navy-band" x1="0" y1="0" x2="1" y2="0">
          <stop offset="0" stop-color="var(--navy)"/>
          <stop offset="1" stop-color="var(--navy-deep)"/>
        </linearGradient>
        <linearGradient id="umber-band" x1="0" y1="1" x2="1" y2="0">
          <stop offset="0" stop-color="var(--umber)"/>
          <stop offset="0.7" stop-color="var(--umber)"/>
          <stop offset="1" stop-color="var(--umber-light)"/>
        </linearGradient>
        <linearGradient id="foot-light" x1="0" y1="0" x2="1" y2="0">
          <stop offset="0" stop-color="var(--taupe-light)"/>
          <stop offset="1" stop-color="var(--taupe-mid)" stop-opacity="0"/>
        </linearGradient>
      </defs>
      <rect class="card-ground" x="0" y="0" width="258" height="143" fill="url(#taupe-ground)"/>
      <path class="silver-crescent" d="M203,0 L258,0 L258,143 L238,143 C252,90 242,32 203,0 Z" fill="url(#silver)"/>
      <path class="navy-swoosh" d="M0,109 C80,126 170,118 215,99 C236,89 248,71 254,48 C250,92 218,124 170,143 L0,143 Z" fill="url(#navy-band)"/>
      <path class="umber-swoosh" d="M150,143 C205,128 240,100 258,62 L258,143 Z" fill="url(#umber-band)"/>
      <path class="foot-highlight" d="M0,138 C50,141 100,141 150,137 L150,143 L0,143 Z" fill="url(#foot-light)"/>
    </svg>

    <p class="brand-name">Corvella</p>

    <div class="practitioner">
      <p class="practitioner-name">NEL</p>
      <p class="credential">BA (Psych)</p>
      <p class="credential">BSc (Hons) Psychology</p>
      <p class="mobile">Mobile:0412 903 618</p>
    </div>

    <p class="tagline">specialising in psychotherapy</p>
  </section>
</main>
</body>
</html>
```